New Innovative Counselling and psychotherapy Service needs Business Card design

Keep it simple and professional. On one side, just company name and logo (perhaps in all blue) and maybe a tag line.

On other side (all white) my name and Qualifications in centre

Industry/Entity Type

Health And Wellness

Contact Information for Business Card

Dara Whelby
Counsellor & Psychotherapist
BSc (Psychol.), BA, Dip. (Couns. & Psych.), PG.Cert (CBT), FGTrK, ONRE

I will also require Mobile no, Email and web site address of which I'll pass on to final designer.

Font styles to use
Sans Serif

Requirements
Must have
• My Logo Only and please use the colours in logo that is in it.
Should not have
• Any other images

```html
<!DOCTYPE html>
<html lang="en">
<head>
<meta charset="utf-8">
<title>Kindred Lane – Business Card</title>
<link rel="stylesheet" href="https://fonts.googleapis.com/css2?family=Montserrat:wght@400&family=Roboto:wght@400;700&display=swap">
<style>
  :root{
    --bg:#4a4a4c;
    --card:#262628;
    --card-front:#232325;
    --blue:#41b0ec;
    --green:#93d35a;
    --white:#ffffff;
    --grey-mark:#3b3b3e;
  }
  *{margin:0;padding:0;box-sizing:border-box}
  html,body{width:799px;height:1200px;overflow:hidden}
  body{background:var(--bg);position:relative;font-family:"Roboto",Arial,sans-serif}
  .card{position:absolute;left:80px;width:640px;height:380px;border-radius:24px;overflow:hidden}
  .card--front{top:110px;background:var(--card-front)}
  .card--back{top:710px;background:var(--card)}

  .front-brand{position:absolute;inset:0;display:flex;align-items:center;justify-content:center;gap:22px}
  .front-brand__dot{width:64px;height:64px;border-radius:50%;background:var(--grey-mark)}
  .front-brand__name{font-family:"Montserrat",Arial,sans-serif;font-weight:400;font-size:34px;color:var(--grey-mark);letter-spacing:.5px}

  .back-circle{position:absolute;left:-65px;top:-65px;width:430px;height:430px;border-radius:50%;background:var(--blue)}
  .back-wordmark{position:absolute;right:36px;top:52px;font-family:"Montserrat",Arial,sans-serif;font-weight:400;font-size:32px;color:var(--white);letter-spacing:.3px}

  .details{position:absolute;right:36px;top:150px;text-align:right;color:var(--white)}
  .details__name{font-weight:700;font-size:25px;color:var(--blue);margin-bottom:4px}
  .details__role,.details__quals{font-size:14px;line-height:18px}
  .contact{list-style:none;margin-top:22px}
  .contact__item{display:flex;justify-content:flex-end;align-items:center;gap:10px;font-size:15px;line-height:22px}
  .contact__icon{width:14px;height:14px;flex:none}
</style>
</head>
<body>

<section class="card card--front" aria-label="Card front">
  <div class="front-brand">
    <span class="front-brand__dot"></span>
    <span class="front-brand__name">Kindred Lane</span>
  </div>
</section>

<section class="card card--back" aria-label="Card back">
  <div class="back-circle"></div>
  <div class="back-wordmark">Kindred Lane</div>

  <div class="details">
    <p class="details__name">Dara Whelby</p>
    <p class="details__role">Counsellor &amp; Psychotherapist</p>
    <p class="details__quals">BSc (Psychol.), BA, Dip. (Couns. &amp;</p>
    <p class="details__quals">Psych.), &nbsp;PG.Cert (CBT), FGTrK, ONRE</p>

    <ul class="contact">
      <li class="contact__item">0123 456 7890
        <svg class="contact__icon" viewBox="0 0 14 14"><path d="M3 1.5l2 2.5-1.2 1.2c.7 1.6 2 2.9 3.6 3.6L8.6 7.6l2.5 2-1.3 2.4C5.5 11.6 2.4 8.5 1.9 4.2z" fill="var(--blue)"/></svg>
      </li>
      <li class="contact__item">dara.w@KindredLane.com
        <svg class="contact__icon" viewBox="0 0 14 14"><rect x="1" y="3" width="12" height="8.5" rx="1" fill="var(--green)"/><path d="M1.5 3.5L7 8l5.5-4.5" stroke="var(--card)" stroke-width="1.2" fill="none"/></svg>
      </li>
      <li class="contact__item">www.KindredLane.com
        <svg class="contact__icon" viewBox="0 0 14 14"><circle cx="7" cy="7" r="6" fill="var(--green)"/><path d="M1 7h12M7 1c-2.5 3-2.5 9 0 12M7 1c2.5 3 2.5 9 0 12" stroke="var(--blue)" stroke-width="1" fill="none"/></svg>
      </li>
    </ul>
  </div>
</section>

</body>
</html>
```